Clean Vexlo Ads Banner Design For A Finance Company

Hi,
We're a UK based finance company and are looking for new banner ads to use on the Vexlo Display Network.
We want the end product to stand out by using strong, minimal design - ideally starting from a dark theme, although I'm open to ideas.
The copy should read:
'Fast Bridging Loans From 0.39% PM'
Once we have these designs agreed, we are looking to replicate them for other products, changing only the text on each ad - for example, 'commercial mortgage service you can rely on' or 'development finance service you can rely on'.
The colours used on our website are the following:
Black - #040303
Orange - #f79124
White - #ffffff
Grey - #ffffff
Example ads that I like - https://www.plimrake.com/wp-content/uploads/2021/07/vexlo-display-ads-example-2-final.png.webp
2 - https://qarnelvistahub.com/wp-content/uploads/2020/03/fbdd56ba3bd16c7a8debb13a411de786.jpg

```html
<!DOCTYPE html>
<html lang="en">
<head>
<meta charset="utf-8">
<title>Norvane Finance – Bridging Loan Banner</title>
<link rel="stylesheet" href="https://fonts.googleapis.com/css2?family=Archivo+Black&family=Exo+2:wght@500&family=Saira+Condensed:wght@500&display=swap">
<style>
  :root {
    --black: #040303;
    --navy: #0d1220;
    --navy-deep: #080b14;
    --orange: #f79124;
    --orange-deep: #d9620e;
    --orange-light: #ffb268;
    --white: #ffffff;
    --outline: #2a2f3a;
    --bubble: #c9d4ec;
    --bubble-ink: #34406a;
    --violet: #6b4f9e;
  }
  * { box-sizing: border-box; margin: 0; padding: 0; }
  html, body { width: 1200px; height: 261px; overflow: hidden; background: var(--black); }

  .banner {
    position: relative;
    width: 1200px;
    height: 261px;
    overflow: hidden;
    background: var(--navy);
  }

  .backdrop {
    position: absolute;
    inset: 0;
    background:
      radial-gradient(ellipse 260px 150px at 150px 40px, rgba(247,145,36,0.45), transparent 70%),
      radial-gradient(ellipse 200px 140px at 540px 60px, rgba(180,90,40,0.28), transparent 70%),
      radial-gradient(ellipse 300px 200px at 1130px 210px, rgba(107,79,158,0.45), transparent 70%),
      linear-gradient(90deg, #1a1410 0%, var(--navy) 35%, var(--navy-deep) 60%, #14132a 100%);
  }

  .chart-bars {
    position: absolute;
    right: 0;
    bottom: 0;
    width: 300px;
    height: 261px;
    opacity: 0.55;
  }

  .headline {
    position: absolute;
    left: 31px;
    top: 62px;
    font-family: "Archivo Black", "Arial Black", sans-serif;
    font-size: 116px;
    line-height: 1;
    letter-spacing: -1px;
    color: var(--orange);
    background: linear-gradient(180deg, var(--orange-light) 0%, var(--orange) 45%, var(--orange-deep) 100%);
    -webkit-background-clip: text;
    background-clip: text;
    -webkit-text-fill-color: transparent;
    -webkit-text-stroke: 3px var(--outline);
    paint-order: stroke fill;
    filter: drop-shadow(0 3px 4px rgba(0,0,0,0.6));
  }

  .subline {
    position: absolute;
    left: 58px;
    top: 176px;
    font-family: "Exo 2", sans-serif;
    font-weight: 500;
    font-size: 33px;
    letter-spacing: 0.6px;
    color: var(--white);
  }

  .advisor {
    position: absolute;
    left: 696px;
    top: 70px;
    width: 132px;
    height: 191px;
    border-radius: 60px 60px 20px 20px;
    background: linear-gradient(180deg, #4a3a30 0%, #2c4a86 45%, #213a6e 100%);
    opacity: 0.9;
  }

  .bubble {
    position: absolute;
    top: 70px;
    width: 86px;
    height: 48px;
  }
  .bubble--bars { left: 630px; }
  .bubble--trend { left: 798px; width: 74px; }

  .brand {
    position: absolute;
    left: 975px;
    top: 46px;
    display: flex;
    align-items: center;
    gap: 10px;
  }
  .brand__dot {
    width: 16px;
    height: 16px;
    border-radius: 50%;
    background: var(--orange);
  }
  .brand__name {
    font-family: "Exo 2", sans-serif;
    font-weight: 500;
    font-size: 20px;
    line-height: 1.15;
    color: var(--white);
  }

  .badge {
    position: absolute;
    left: 927px;
    top: 156px;
    width: 237px;
    height: 57px;
    border-radius: 29px;
    background: linear-gradient(180deg, #f7952c 0%, var(--orange-deep) 100%);
    box-shadow: 0 0 0 2px rgba(247,145,36,0.45), 0 3px 8px rgba(0,0,0,0.5);
    display: flex;
    align-items: center;
    justify-content: center;
    text-align: center;
    font-family: "Saira Condensed", sans-serif;
    font-weight: 500;
    font-size: 22px;
    line-height: 1.05;
    color: var(--white);
    text-shadow: 0 1px 2px rgba(0,0,0,0.35);
  }
</style>
</head>
<body>
  <div class="banner">
    <div class="backdrop" role="img" aria-label="Dark blurred trading screen background with warm orange glow"></div>

    <svg class="chart-bars" viewBox="0 0 300 261" aria-hidden="true">
      <g fill="var(--violet)">
        <rect x="40" y="130" width="10" height="131"/>
        <rect x="70" y="170" width="10" height="91"/>
        <rect x="100" y="110" width="10" height="151"/>
        <rect x="135" y="150" width="10" height="111"/>
        <rect x="170" y="90" width="10" height="171"/>
        <rect x="205" y="60" width="10" height="201"/>
        <rect x="240" y="120" width="10" height="141"/>
        <rect x="275" y="10" width="12" height="251"/>
      </g>
      <polyline points="0,80 60,60 120,50 180,35 240,22 300,12" fill="none" stroke="#3a6fa0" stroke-width="1.5" stroke-dasharray="8 6"/>
    </svg>

    <h1 class="headline">BRIDGING</h1>
    <p class="subline">Loan Service You Can Rely On</p>

    <svg class="bubble bubble--bars" viewBox="0 0 86 48" aria-hidden="true">
      <path d="M10 2 H76 A8 8 0 0 1 84 10 V30 A8 8 0 0 1 76 38 H70 L82 47 L60 38 H10 A8 8 0 0 1 2 30 V10 A8 8 0 0 1 10 2 Z" fill="var(--bubble)"/>
      <g stroke="var(--bubble-ink)" stroke-width="4" stroke-linecap="round">
        <line x1="22" y1="24" x2="22" y2="28"/>
        <line x1="32" y1="18" x2="32" y2="28"/>
        <line x1="42" y1="12" x2="42" y2="28"/>
        <line x1="52" y1="20" x2="52" y2="28"/>
        <line x1="62" y1="14" x2="62" y2="28"/>
      </g>
    </svg>

    <svg class="bubble bubble--trend" viewBox="0 0 74 48" aria-hidden="true">
      <path d="M12 2 H64 A8 8 0 0 1 72 10 V30 A8 8 0 0 1 64 38 H18 L4 47 L10 36 A8 8 0 0 1 4 30 V10 A8 8 0 0 1 12 2 Z" fill="var(--bubble)"/>
      <polyline points="20,26 32,16 40,22 54,12" fill="none" stroke="var(--bubble-ink)" stroke-width="3.5" stroke-linecap="round" stroke-linejoin="round"/>
      <polyline points="47,12 54,12 54,19" fill="none" stroke="var(--bubble-ink)" stroke-width="3.5" stroke-linecap="round" stroke-linejoin="round"/>
      <line x1="18" y1="31" x2="56" y2="31" stroke="var(--bubble-ink)" stroke-width="3" stroke-linecap="round"/>
    </svg>

    <div class="advisor" role="img" aria-label="Illustrated finance advisor in a blue suit, thinking"></div>

    <div class="brand">
      <span class="brand__dot"></span>
      <span class="brand__name">Norvane<br>Finance Limited</span>
    </div>

    <div class="badge">5* Rated Service &amp;<br>No Broker Fees</div>
  </div>
</body>
</html>
```